create making it look fantastic

create a name for this product and redesign this quick brochure i put together
GLINT ROVER can not be used as it is already trademarked the word rover

```html
<!DOCTYPE html>
<html lang="en">
<head>
<meta charset="utf-8">
<title>Voltward – Safety Flyer</title>
<link rel="stylesheet" href="https://fonts.googleapis.com/css2?family=Anton&family=Poppins:wght@400;500;600;700;800&display=swap">
<style>
  :root{
    --purple:#2e1a57;
    --orange:#f47b20;
    --red:#b3141c;
    --ink:#1f1f2a;
    --grey-row:#ececec;
    --page:#e9e9eb;
    --white:#ffffff;
  }
  *{box-sizing:border-box;margin:0;padding:0}
  html,body{width:1200px;height:3034px;overflow:hidden;background:var(--page);font-family:"Poppins",sans-serif;color:var(--ink)}
  .flyer{position:absolute;left:105px;top:876px;width:990px;height:1282px;background:var(--white);overflow:hidden;box-shadow:0 8px 30px rgba(0,0,0,.15)}
  .abs{position:absolute}

  .brand{left:86px;top:72px;display:flex;align-items:center;gap:14px;font-weight:800;font-size:64px;letter-spacing:2px;color:var(--purple)}
  .brand-mark{width:26px;height:26px;background:var(--orange)}

  .headline{left:84px;top:250px;font-family:"Anton",sans-serif;font-weight:400;line-height:.92;color:var(--purple);text-transform:uppercase}
  .headline .big{font-size:92px;display:block}
  .headline .accent{font-size:60px;color:var(--orange);display:block;margin-top:6px}
  .tagline{left:87px;top:494px;font-size:26px;font-weight:500;letter-spacing:.3px;color:var(--ink)}

  .hero-art{left:460px;top:38px;width:540px;height:500px}
  .new-badge{left:697px;top:52px;width:140px;height:140px}

  .section-title{font-weight:700;font-size:26px;color:var(--purple)}
  .application{left:84px;top:578px;width:400px}
  .application ul{list-style:none;margin-top:12px}
  .application li{position:relative;padding-left:26px;font-size:16px;line-height:1.2;margin-bottom:10px}
  .application li::before{content:"";position:absolute;left:0;top:5px;width:13px;height:13px;border-radius:50%;background:var(--orange)}

  .spec-tab{left:83px;top:848px;width:294px;height:56px;background:var(--orange);clip-path:polygon(0 0,88% 0,100% 100%,0 100%);color:var(--white);font-weight:700;font-size:24px;padding:12px 0 0 28px}
  .spec-table{left:83px;top:904px;width:396px}
  .spec-row{height:27px;font-size:13px;padding:4px 20px;border:1px solid #cfcfcf}
  .spec-row:nth-child(odd){background:var(--grey-row);border-color:var(--grey-row)}

  .sentry-band{left:83px;top:1106px;width:390px;height:64px}
  .sentry-band .left{position:absolute;left:0;top:8px;width:200px;height:48px;background:var(--orange);clip-path:polygon(4% 0,100% 0,100% 100%,0 100%);color:var(--white);font-weight:700;font-size:30px;line-height:48px;padding-left:24px}
  .sentry-band .right{position:absolute;left:200px;top:8px;width:190px;height:48px;background:var(--purple);clip-path:polygon(0 0,100% 0,96% 100%,0 100%);color:var(--white);font-weight:700;font-size:30px;line-height:48px;padding-left:54px}
  .sentry-band .clock{position:absolute;left:184px;top:0;width:64px;height:64px}

  .features{left:532px;top:589px;width:377px;height:453px;background:var(--purple);padding:14px 20px 0 50px;color:var(--white)}
  .features h2{font-weight:700;font-size:25px;color:var(--orange);margin-left:-24px}
  .feature{height:66px;border-bottom:1px solid rgba(255,255,255,.18);display:flex;align-items:center;font-size:16px;line-height:1.2}
  .feature:last-child{border-bottom:none}
  .feature b{color:var(--orange);font-weight:700}
  .feature-icons{left:510px;top:654px;width:44px}
  .feature-icon{width:44px;height:44px;border-radius:50%;background:var(--white);border:3px solid #e1e1e6;box-shadow:0 2px 5px rgba(0,0,0,.25);margin-bottom:22px;display:flex;align-items:center;justify-content:center}

  .danger-card{left:530px;top:1073px;width:379px;height:108px;border:2px solid #d6d6d6;border-radius:6px;background:var(--white);box-shadow:0 4px 8px rgba(0,0,0,.15)}
  .danger-sign{position:absolute;left:18px;top:12px;width:140px;height:80px;border-radius:8px;background:linear-gradient(#d21f26,#8f0d12);color:var(--white);font-family:"Anton",sans-serif;font-size:30px;text-align:center;padding-top:36px;line-height:1}
  .danger-text{position:absolute;left:178px;top:12px;font-weight:700;line-height:1.1}
  .danger-text .warn{color:var(--orange);font-size:19px}
  .danger-text .note{color:var(--ink);font-size:14px}
  .screw{position:absolute;width:9px;height:9px;border-radius:50%;background:#777}

  .footer-line{left:0;top:1276px;width:990px;height:6px;background:var(--orange)}
  .footer-phone{left:0;top:1192px;width:380px;height:90px;background:var(--orange);clip-path:polygon(0 0,86% 0,100% 100%,0 100%);color:var(--white);font-weight:800;font-size:35px;display:flex;align-items:center;padding-left:56px;gap:8px}
  .footer-contact{left:380px;top:1228px;font-size:18px;display:flex;gap:18px;align-items:center;color:var(--ink)}
  .footer-contact span{display:flex;align-items:center;gap:6px}
</style>
</head>
<body>
<main class="flyer">

  <div class="abs brand"><span class="brand-mark"></span>VOLTWARD</div>

  <svg class="abs hero-art" viewBox="0 0 540 500">
    <defs>
      <linearGradient id="panelShade" x1="0" y1="0" x2="1" y2="1">
        <stop offset="0" stop-color="#5b5f69"/>
        <stop offset="1" stop-color="#1f2127"/>
      </linearGradient>
    </defs>
    <circle cx="270" cy="244" r="220" fill="none" stroke="var(--purple)" stroke-width="44"/>
    <polygon points="430,100 500,30 540,30 540,80 470,150" fill="var(--orange)"/>
    <polygon points="440,370 500,320 540,360 540,400 490,440" fill="var(--orange)"/>
    <polygon role="img" aria-label="Photo of a dark grey tempered glass double power outlet" points="120,110 500,160 455,440 80,360" fill="url(#panelShade)"/>
  </svg>

  <svg class="abs new-badge" viewBox="0 0 140 140">
    <circle cx="70" cy="70" r="68" fill="var(--red)"/>
    <circle cx="70" cy="70" r="56" fill="none" stroke="#f3c9cb" stroke-width="1.5" stroke-dasharray="3 3"/>
    <text x="70" y="88" text-anchor="middle" font-family="Anton, sans-serif" font-size="48" fill="#fff">NEW</text>
  </svg>

  <h1 class="abs headline">
    <span class="big">Your</span>
    <span class="big">Safety is</span>
    <span class="accent">Our Commitment</span>
  </h1>
  <p class="abs tagline">PRIORITIZING YOUR SAFETY ABOVE ALL</p>

  <section class="abs application">
    <h2 class="section-title">APPLICATION</h2>
    <ul>
      <li>Our GPO is easily installed by a registered electrician and once it is turned on and customised, it will only operate for up to 8 hours.</li>
      <li>Prevent the risk to your environment of battery operated wheelchairs and scooters.</li>
      <li>The 8-Hour Sentry keeps a battery operating equipment safe from overheating and possibly exploding.</li>
    </ul>
  </section>

  <div class="abs spec-tab">SPECIFICATIONS</div>
  <div class="abs spec-table">
    <div class="spec-row">Colours available with and black.</div>
    <div class="spec-row">Size 120 x 72 x 42mm.</div>
    <div class="spec-row">Capacitive easy touch power on button.</div>
    <div class="spec-row">Operating Voltage: 110-240V</div>
    <div class="spec-row">AC/50Hz-60Hz.</div>
    <div class="spec-row">Rated Current: 10A x 2</div>
    <div class="spec-row">Material: toughened glass panel+ fire retardant shell</div>
  </div>

  <div class="abs sentry-band">
    <div class="left">8-HOUR</div>
    <div class="right">SENTRY</div>
    <svg class="clock" viewBox="0 0 64 64">
      <circle cx="32" cy="32" r="31" fill="#fff" stroke="var(--orange)" stroke-width="2"/>
      <circle cx="32" cy="32" r="22" fill="none" stroke="#555" stroke-width="2"/>
      <path d="M32 18v14l9 6" fill="none" stroke="#333" stroke-width="2.5" stroke-linecap="round"/>
    </svg>
  </div>

  <section class="abs features">
    <h2>FEATURES</h2>
    <div class="feature"><span><b>FIRE</b> retardent double GPO made<br>with V0 material.</span></div>
    <div class="feature"><span>Tempered glass panel <b>easily cleaned<br>and never fades.</b></span></div>
    <div class="feature"><span>Capacitive <b>easy touch</b> power<br>on button.</span></div>
    <div class="feature"><span>MCU Intelligent Smart Chipset,<br><b>3 Year Warranty.</b></span></div>
    <div class="feature"><span>Automatic cut-off of power <b>2 hours<br>(can be customised).</b></span></div>
    <div class="feature"><span>Complies with <b>Australian Standards</b><br>and Approvals</span></div>
  </section>
  <div class="abs feature-icons">
    <div class="feature-icon"><svg width="20" height="20" viewBox="0 0 20 20"><path d="M10 2c3 4 6 6 6 10a6 6 0 0 1-12 0c0-3 2-4 3-7 1 2 2 2 3 3z" fill="var(--orange)"/></svg></div>
    <div class="feature-icon"><svg width="20" height="20" viewBox="0 0 20 20"><rect x="3" y="3" width="14" height="14" rx="3" fill="var(--purple)"/></svg></div>
    <div class="feature-icon"><svg width="20" height="20" viewBox="0 0 20 20"><path d="M8 2v10l-2-2-2 2 5 6h7v-7l-6-2V2z" fill="var(--purple)"/></svg></div>
    <div class="feature-icon"><svg width="20" height="20" viewBox="0 0 20 20"><path d="M10 1l7 3v6c0 5-4 8-7 9-3-1-7-4-7-9V4z" fill="var(--purple)"/></svg></div>
    <div class="feature-icon"><svg width="20" height="20" viewBox="0 0 20 20"><circle cx="10" cy="11" r="7" fill="none" stroke="var(--purple)" stroke-width="2.5"/><path d="M10 2v8" stroke="var(--orange)" stroke-width="2.5"/></svg></div>
    <div class="feature-icon"><svg width="20" height="20" viewBox="0 0 20 20"><rect x="4" y="2" width="12" height="15" rx="1" fill="var(--purple)"/><path d="M7 7h6M7 10h6" stroke="#fff" stroke-width="1.5"/></svg></div>
  </div>

  <div class="abs danger-card">
    <span class="screw" style="left:5px;top:5px"></span>
    <span class="screw" style="right:5px;top:5px"></span>
    <span class="screw" style="left:5px;bottom:5px"></span>
    <span class="screw" style="right:5px;bottom:5px"></span>
    <div class="danger-sign">
      <svg style="position:absolute;left:56px;top:6px" width="28" height="26" viewBox="0 0 28 26"><path d="M14 1L27 25H1z" fill="#fff"/><path d="M14 9v8M14 20v2" stroke="var(--red)" stroke-width="3"/></svg>
      DANGER
    </div>
    <div class="danger-text">
      <div class="warn">RISK OF BATTERY<br>EXPLOSION</div>
      <div class="note">NO SMOKING<br>SPARKS OR FLAMES</div>
    </div>
  </div>

  <div class="abs footer-line"></div>
  <div class="abs footer-phone">
    <svg width="30" height="30" viewBox="0 0 30 30"><circle cx="15" cy="15" r="14" fill="var(--purple)"/><path d="M10 8l3 0 1 4-2 1a9 9 0 0 0 5 5l1-2 4 1v3c0 1-1 2-2 2A14 14 0 0 1 8 10c0-1 1-2 2-2z" fill="#fff"/></svg>
    1300 246 810
  </div>
  <div class="abs footer-contact">
    <span><svg width="18" height="16" viewBox="0 0 18 16"><rect x="1" y="2" width="16" height="12" fill="var(--purple)"/><path d="M1 2l8 6 8-6" fill="none" stroke="#fff" stroke-width="1.5"/></svg>info@voltward.com.au</span>
    <span><svg width="18" height="18" viewBox="0 0 18 18"><circle cx="9" cy="9" r="8" fill="none" stroke="var(--purple)" stroke-width="2"/><path d="M1 9h16M9 1c-3 4-3 12 0 16M9 1c3 4 3 12 0 16" fill="none" stroke="var(--purple)" stroke-width="1.5"/></svg>www.voltward.com.au</span>
  </div>

</main>
</body>
</html>
```